FinTech company looking to revamp and expand client-facing interface for our financial models

Pellworth Engines currently has a very simple website that allows clients to interact with our financial models. We are looking to completely redesign the current site and add several extra pages to provide extra functionality. We want the design to have a modern, slick feel, that will work on both a desktop or a tablet. It should be straightforward for clients to move between different pages at any time, and clear from the layout how to interact with the more advanced features. We have included screenshots of existing pages in the attached design brief, as well as sketches of the functionality required by the new pages, but can't provide a direct link to the current site.
Target Market(s)
Professional investors that will be paying to access the interface
Industry/Entity Type
Finance
Number of Pages Required
4 page
Colors
Designer to choose colors to be used in the design.
Look and feel
Each slider illustrates characteristics of the customer's brand and the style your logo design should communicate.

```html
<!DOCTYPE html>
<html lang="en">
<head>
<meta charset="utf-8">
<title>Pellworth Engines – Model Interface</title>
<link href="https://fonts.googleapis.com/css2?family=Poppins:wght@400;500;600;700&display=swap" rel="stylesheet">
<style>
:root{
  --stage:#7b7b7b;
  --bar:#1e1e1e;
  --bar-deep:#111111;
  --subbar:#2c2c2c;
  --teal:#35b7a2;
  --teal-dark:#1f6b5f;
  --row-alt:#ecf6f4;
  --ink:#222;
  --muted:#555;
  --line:#dcdcdc;
  --soft:#efefef;
  --white:#fff;
}
*{box-sizing:border-box;margin:0;padding:0}
html,body{width:1200px;height:4093px;overflow:hidden}
body{background:var(--stage);font-family:'Poppins',sans-serif;color:var(--ink);position:relative}
.app{position:absolute;background:var(--white);overflow:hidden}
.topbar{height:40px;background:var(--bar);position:relative;display:flex;font-size:10.5px;font-weight:600;color:#fff;letter-spacing:.3px}
.tab{display:flex;align-items:center;justify-content:center;width:56px}
.tab.first{width:84px}
.tab.active{background:var(--teal)}
.brand{position:absolute;top:0;height:40px;line-height:40px;font-size:12px;font-weight:600;letter-spacing:.5px}
.usermenu{position:absolute;right:0;top:0;height:40px;background:var(--bar-deep);display:flex;align-items:center;justify-content:space-around;padding:0 14px;font-size:10px}
.usermenu .on{color:var(--teal)}
.subbar{height:41px;background:var(--subbar);position:relative;color:#fff;font-size:10.5px;font-weight:500}
.subbar span{position:absolute;top:13px}
.subbar .on{color:var(--teal)}
.subbar .plus{color:var(--teal);font-size:15px;top:9px;font-weight:600}
.export{position:absolute;color:var(--teal);font-size:10.5px;font-weight:600}
.caption{position:absolute;font-size:10.5px;font-weight:600;text-transform:uppercase}
table.grid{position:absolute;border-collapse:collapse;font-size:11px}
.grid th{background:var(--teal);color:#fff;font-weight:500;text-align:left;padding:0 8px;height:42px;border-right:1px solid #fff}
.grid td{padding:0 8px;height:44px;border-right:1px solid var(--line);line-height:1.15}
.grid tr:nth-child(even) td{background:var(--row-alt)}
.grid tr:last-child td{border-bottom:1px solid var(--line)}
.footer{position:absolute;left:0;right:0;text-align:center;font-size:11px;color:#333}
.grey{position:absolute;background:var(--soft)}
.chartbox{position:absolute;background:#fff}
.filters{position:absolute;left:0;top:81px;width:218px;height:254px;background:rgba(40,40,40,.88);color:#fff;font-size:10.5px;padding:14px 22px}
.filters label{display:block;font-weight:600;margin-top:10px}
.filters .field{width:86px;height:20px;background:#fff;color:#222;font-size:9px;padding:3px 6px;margin-top:4px}
.filters .checks{display:flex;gap:14px;margin-top:10px;align-items:center}
.box{display:inline-block;width:14px;height:14px;background:#fff;vertical-align:middle;margin-right:6px}
.btn{display:inline-block;background:var(--teal);color:#fff;font-weight:600;font-size:10px;padding:7px 24px;margin-top:12px}
.card{position:absolute;background:#fff;border:1px solid var(--line)}
.mini{font-size:10.5px}
</style>
</head>
<body>

<!-- Models overview -->
<section class="app" style="left:100px;top:92px;width:1000px;height:513px">
  <header class="topbar" style="margin-top:24px">
    <div class="tab first">QBOSS</div><div class="tab active">250D</div><div class="tab">83D</div><div class="tab">42D</div>
    <div class="brand" style="left:384px">PELLWORTH</div>
    <nav class="usermenu" style="width:320px"><span class="on">▣ MODELS</span><span>⚙ SENSITIVITIES</span><span>|</span><span>★ FAVORITES</span></nav>
  </header>
  <nav class="subbar"><span style="left:420px">» EQUITIES</span><span style="left:537px">» ETFS</span><span style="left:636px">» PAIRS</span><span style="left:740px" class="on">» ETF PAIRS</span><span style="left:864px">» FACTORS</span><span class="plus" style="left:950px">+</span></nav>
  <div class="export" style="left:20px;top:119px">⇨ EXPORT</div>
  <table class="grid" style="left:21px;top:147px;width:955px">
    <tr><th>ID</th><th>SECTOR</th><th>TIME</th><th>QUALITY</th><th>STAT 1</th><th>STAT 2</th><th>STAT 3</th><th>STAT 4</th><th>STAT 5</th><th>STAT 6</th><th>STAT 7</th><th>STAT 8</th></tr>
    <tr><td>Model 1</td><td>Materials</td><td>2019-07-03<br>12:15:00.000</td><td>30.2288</td><td>2.01574</td><td>23.305</td><td>-0.149368</td><td>22.3054</td><td>4.63714</td><td>0.945706</td><td>2.81949</td><td>2.60858</td></tr>
    <tr><td>Model 2</td><td>Industrials</td><td>2019-07-03<br>12:15:00.000</td><td>32.8694</td><td>0.87307</td><td>32.185</td><td>-0.0336927</td><td>33.9911</td><td>11.5693</td><td>-0.472968</td><td>-0.830458</td><td>6.80646</td></tr>
    <tr><td>Model 3</td><td>Consumer<br>Discretionary</td><td>2019-07-03<br>12:15:00.000</td><td>1.66002</td><td>-0.569222</td><td>159.814</td><td>0.0252328</td><td>172.616</td><td>10.2875</td><td>-0.750396</td><td>-0.385309</td><td>4.69146</td></tr>
    <tr><td>Model 4</td><td>Information<br>Technology</td><td>2019-07-03<br>12:15:00.000</td><td>45.6856</td><td>0.412148</td><td>202.488</td><td>0.00849232</td><td>205.834</td><td>11.9094</td><td>-0.137913</td><td>0.449595</td><td>3.85106</td></tr>
    <tr><td>Model 5</td><td>Information<br>Technology</td><td>2019-07-03<br>12:15:00.000</td><td>75.7733</td><td>7.06728</td><td>188.605</td><td>0.016913</td><td>181.665</td><td>3.82241</td><td>0.981019</td><td>1.29847</td><td>3.34927</td></tr>
  </table>
  <p class="footer" style="top:436px">© Copyrights 2019 Pellworth | All Rights Reserved</p>
</section>

<!-- Factors with filters -->
<section class="app" style="left:180px;top:683px;width:839px;height:437px">
  <header class="topbar" style="margin-top:19px">
    <div class="tab first" style="width:90px">FACTORS</div><div class="tab active">250D</div><div class="tab">83D</div><div class="tab">42D</div>
    <div class="brand" style="left:330px">PELLWORTH</div>
    <nav class="usermenu" style="width:312px"><span class="on">▣ MODELS</span><span>⚙ SENSITIVITIES</span><span>|</span><span>★ FAVORITES</span></nav>
  </header>
  <nav class="subbar"><span class="on" style="left:24px">FILTERS ⊙</span><span style="left:265px">» EQUITIES</span><span style="left:383px">» ETFS</span><span style="left:482px">» PAIRS</span><span style="left:586px">» ETF PAIRS</span><span style="left:710px">» FACTORS</span><span class="plus" style="left:807px">+</span></nav>
  <table class="grid" style="left:21px;top:138px;width:797px">
    <tr><th>FACTOR</th><th>MODEL</th><th>SECTOR</th><th>STAT 1</th><th>STAT 2</th><th>STAT 3</th><th>STAT 4</th><th>STAT 5</th><th>STAT 6</th></tr>
    <tr><td>Factor 1</td><td>Model 1</td><td>Materials</td><td>-1.4</td><td>0.1</td><td>-3.1</td><td>0.7</td><td>30.2</td><td>0.9</td></tr>
    <tr><td>Factor 2</td><td>Model 1</td><td>Materials</td><td>2.8</td><td>0.1</td><td>6.1</td><td>100</td><td>30.2</td><td>0.9</td></tr>
    <tr><td>Factor 3</td><td>Model 1</td><td>Materials</td><td>-3.7</td><td>2.7</td><td>-7.2</td><td>100</td><td>30.2</td><td>0.9</td></tr>
    <tr><td>Factor 1</td><td>Model 2</td><td>Industrials</td><td>2.8</td><td>0.2</td><td>2.7</td><td>0.5</td><td>32.9</td><td>-0.5</td></tr>
    <tr><td>Factor 2</td><td>Model 2</td><td>Industrials</td><td>0.8</td><td>0.3</td><td>2.5</td><td>0.5</td><td>32.9</td><td>-0.5</td></tr>
  </table>
  <aside class="filters">
    <div style="color:#777;font-size:9px">⇨ EXPORT</div>
    <label>QUALITY &nbsp; Threshold</label><div class="field">-10</div>
    <label>ABS. STAT Threshold</label><div class="field">-10</div>
    <label>Apply filter</label>
    <div class="checks"><span><i class="box"></i>All tabs</span><span><i class="box"></i>Current tabs</span></div>
    <span class="btn">SEARCH</span>
  </aside>
  <p class="footer" style="top:400px">© Copyrights 2019 Pellworth | All Rights Reserved</p>
</section>

<!-- ETF pairs: selected factors and charts -->
<section class="app" style="left:180px;top:1197px;width:839px;height:1339px">
  <header class="topbar" style="margin-top:19px">
    <div class="tab first" style="width:90px">FACTORS</div><div class="tab active">250D</div><div class="tab">83D</div><div class="tab">42D</div>
    <div class="brand" style="left:384px">PELLWORTH</div>
    <nav class="usermenu" style="width:312px"><span>▣ MODELS</span><span>⚙ SENSITIVITIES</span><span>|</span><span>★ FAVORITES</span></nav>
  </header>
  <nav class="subbar"><span style="left:265px">» EQUITIES</span><span style="left:383px">» ETFS</span><span style="left:482px">» PAIRS</span><span class="on" style="left:586px">» ETF PAIRS</span><span style="left:710px">» FACTORS</span><span class="plus" style="left:807px">+</span></nav>
  <div class="export" style="left:20px;top:112px">⇨ EXPORT</div>
  <div class="caption" style="left:20px;top:134px">Number of selected factors: 3</div>
  <div class="caption" style="right:24px;top:134px">Computed at : 2019-07-02 , 20:15:00:000</div>
  <table class="grid" style="left:21px;top:157px;width:797px">
    <tr><th>ID</th><th>STAT 1</th><th>STAT 2</th><th>STAT 3</th><th>STAT 4</th></tr>
    <tr><td>FACTOR 1</td><td>2.8</td><td>0.0094</td><td>6.1</td><td>100</td></tr>
    <tr><td>FACTOR 2</td><td>-1.4</td><td>0.085</td><td>-3.1</td><td>0.7</td></tr>
    <tr><td>FACTOR 3</td><td>-3.7</td><td>2.72</td><td>-7.2</td><td>100</td></tr>
  </table>
  <div class="caption" style="left:20px;top:350px">Unselected factors</div>
  <table class="grid" style="left:21px;top:373px;width:797px">
    <tr><th>FACTOR</th><th>FACTOR</th><th>FACTOR</th><th>FACTOR</th><th>FACTOR</th></tr>
    <tr><td>FACTOR</td><td>FACTOR</td><td></td><td></td><td></td></tr>
  </table>
  <div class="grey" style="left:0;top:469px;width:839px;height:870px"></div>

  <div class="chartbox" style="left:164px;top:515px;width:510px;height:402px">
    <svg width="510" height="402" viewBox="0 0 510 402" font-size="6" fill="#666">
      <g stroke="#e4e4e4"><line x1="28" y1="30" x2="480" y2="30"/><line x1="28" y1="60" x2="480" y2="60"/><line x1="28" y1="90" x2="480" y2="90"/><line x1="28" y1="120" x2="480" y2="120"/><line x1="28" y1="150" x2="480" y2="150"/></g>
      <polyline fill="none" stroke="#3b4a8c" stroke-width="1" points="28,35 50,45 70,42 90,55 110,52 130,70 150,66 170,85 190,80 210,100 230,96 250,110 270,104 290,118 310,114 330,126 350,122 370,134 390,130 410,138 430,140 450,136 470,142 480,140"/>
      <polyline fill="none" stroke="#8ab06a" stroke-width="1" points="28,50 50,58 70,55 90,66 110,70 130,86 150,82 170,100 190,104 210,116 230,112 250,122 270,118 290,128 310,124 330,132 350,130 370,138 390,134 410,142 430,144 450,140 470,146 480,144"/>
      <text x="40" y="165">Aug 2018</text><text x="95" y="165">Oct 2018</text><text x="150" y="165">Dec 2018</text><text x="210" y="165">Feb 2019</text><text x="270" y="165">Apr 2019</text><text x="330" y="165">May 2019</text><text x="420" y="165">Jul 2019</text>
      <g stroke="#e4e4e4"><line x1="28" y1="260" x2="480" y2="260"/><line x1="28" y1="292" x2="480" y2="292"/><line x1="28" y1="324" x2="480" y2="324"/><line x1="28" y1="356" x2="480" y2="356"/></g>
      <polyline fill="none" stroke="#888" stroke-width="1" points="28,330 45,340 60,320 75,350 95,330 115,355 135,340 155,358 175,330 195,345 215,320 235,330 255,300 275,310 295,285 315,295 335,275 355,285 375,270 395,280 415,265 435,272 455,258 480,262"/>
      <text x="40" y="244">Aug 2018</text><text x="95" y="244">Oct 2018</text><text x="150" y="244">Dec 2018</text><text x="210" y="244">Feb 2019</text><text x="270" y="244">Apr 2019</text><text x="420" y="244">Jul 2019</text>
      <text x="40" y="380">Aug 2018</text><text x="150" y="380">Dec 2018</text><text x="270" y="380">Apr 2019</text><text x="420" y="380">Jul 2019</text>
    </svg>
  </div>

  <div class="chartbox" style="left:164px;top:949px;width:510px;height:146px">
    <svg width="510" height="146" viewBox="0 0 510 146" font-size="6" fill="#666">
      <line x1="28" y1="73" x2="450" y2="73" stroke="#ddd"/>
      <polyline fill="none" stroke="#c9b800" stroke-width="5" stroke-dasharray="2 2" points="55,50 120,48 160,46 200,50 240,44 300,42 360,46 420,50 450,52"/>
      <polyline fill="none" stroke="#2a4a8a" stroke-width="5" stroke-dasharray="2 2" points="55,95 120,96 160,98 200,96 240,100 300,102 360,100 420,98 450,97"/>
      <text x="456" y="30">Pairs</text>
      <text x="40" y="130">Jul 2018</text><text x="150" y="130">Nov 2018</text><text x="270" y="130">Mar 2019</text><text x="400" y="130">Jul 2019</text>
    </svg>
  </div>

  <div class="chartbox" style="left:151px;top:1144px;width:512px;height:195px">
    <svg width="512" height="150" viewBox="0 0 512 150" font-size="6" fill="#666">
      <g fill="#2a5aa8"><circle cx="80" cy="70" r="2.5"/><circle cx="90" cy="80" r="2.5"/><circle cx="110" cy="60" r="2.5"/><circle cx="140" cy="90" r="2.5"/><circle cx="170" cy="75" r="2.5"/><circle cx="200" cy="85" r="2.5"/><circle cx="225" cy="95" r="2.5"/></g>
      <g fill="#c9b800"><circle cx="85" cy="60" r="2.5"/><circle cx="120" cy="75" r="2.5"/><circle cx="150" cy="55" r="2.5"/><circle cx="180" cy="95" r="2.5"/><circle cx="210" cy="70" r="2.5"/><circle cx="265" cy="60" r="2.5"/><circle cx="270" cy="80" r="2.5"/></g>
      <line x1="75" y1="40" x2="130" y2="40" stroke="#2a5aa8" stroke-width="3"/>
      <line x1="220" y1="40" x2="420" y2="40" stroke="#2a5aa8" stroke-width="3"/>
      <text x="460" y="38">Pairs</text>
      <text x="55" y="130">Jul 2018</text><text x="160" y="130">Nov 2018</text><text x="290" y="130">Mar 2019</text><text x="410" y="130">Jul 2019</text>
    </svg>
  </div>
  <p class="footer" style="top:1315px">© Copyrights 2019 Pellworth | All Rights Reserved</p>
</section>

<!-- Portfolio builder -->
<section class="app" style="left:180px;top:2617px;width:839px;height:526px">
  <header class="topbar" style="margin-top:19px">
    <div class="tab first" style="width:90px">FACTORS</div><div class="tab active">250D</div><div class="tab">83D</div><div class="tab">42D</div>
    <div class="brand" style="left:384px">PELLWORTH</div>
    <nav class="usermenu" style="width:312px"><span>▣ MODELS</span><span>⚙ SENSITIVITIES</span><span>|</span><span>★ FAVORITES</span></nav>
  </header>
  <nav class="subbar"><span style="left:265px">» EQUITIES</span><span style="left:383px">» ETFS</span><span style="left:482px">» PAIRS</span><span class="on" style="left:586px">» ETF PAIRS</span><span style="left:710px">» FACTORS</span><span class="plus" style="left:807px">+</span></nav>
  <div class="export" style="left:20px;top:112px">⇨ EXPORT</div>
  <div class="caption" style="left:20px;top:134px">Number of selected factors: 3</div>
  <div class="caption" style="right:24px;top:134px">Computed at : 2019-07-02 , 20:15:00:000</div>
  <table class="grid" style="left:108px;top:205px;width:240px">
    <tr><th>⊝ &nbsp;NAME</th><th>SIZE</th></tr>
    <tr><td>⊝ &nbsp;MEMBER 1</td><td>0.2</td></tr>
    <tr><td>⊝ &nbsp;MEMBER 2</td><td>0.5</td></tr>
    <tr><td>⊝ &nbsp;MEMBER 3</td><td>-0.3</td></tr>
  </table>
  <div class="mini" style="position:absolute;left:116px;top:401px;display:flex;align-items:center;gap:8px">⊞ Add Members <span style="border:1px solid var(--line);width:110px;padding:4px 8px;color:#888;font-size:9px">Search</span></div>
  <div class="mini" style="position:absolute;left:116px;top:436px">⊟ Save Portfolio</div>
  <svg style="position:absolute;left:420px;top:198px" width="330" height="200" viewBox="0 0 330 200" font-size="11" fill="#222">
    <line x1="100" y1="0" x2="100" y2="180" stroke="#555"/>
    <line x1="0" y1="180" x2="310" y2="180" stroke="#ccc"/>
    <rect x="100" y="48" width="102" height="18" fill="var(--teal)"/><text x="85" y="61">A</text>
    <rect x="100" y="90" width="184" height="18" fill="var(--teal-dark)"/><text x="85" y="103">B</text>
    <rect x="42" y="132" width="58" height="18" fill="var(--teal)"/><text x="85" y="145" fill="#222">C</text>
    <text x="25" y="196">-0.3</text><text x="193" y="196">0.2</text><text x="277" y="196">0.5</text>
  </svg>
  <p class="footer" style="top:499px">© Copyrights 2019 Pellworth | All Rights Reserved</p>
</section>

<!-- Mode runner -->
<section class="app" style="left:180px;top:3232px;width:839px;height:753px">
  <header class="topbar" style="margin-top:19px">
    <div class="tab first" style="width:90px">FACTORS</div><div class="tab active">250D</div><div class="tab">83D</div><div class="tab">42D</div>
    <div class="brand" style="left:384px">PELLWORTH</div>
    <nav class="usermenu" style="width:312px"><span class="on">▣ MODELS</span><span>⚙ SENSITIVITIES</span><span>|</span><span>★ FAVORITES</span></nav>
  </header>
  <nav class="subbar"><span style="left:265px">» EQUITIES</span><span style="left:383px">» ETFS</span><span style="left:482px">» PAIRS</span><span class="on" style="left:586px">» ETF PAIRS</span><span style="left:710px">» FACTORS</span><span class="plus" style="left:807px">+</span></nav>
  <div class="grey" style="left:0;top:81px;width:839px;height:620px"></div>
  <div class="export" style="left:20px;top:112px">⇨ EXPORT</div>
  <div class="caption" style="left:20px;top:134px">Number of selected factors: 3</div>
  <div class="caption" style="right:24px;top:134px">Computed at : 2019-07-02 , 20:15:00:000</div>

  <div class="card" style="left:119px;top:183px;width:240px;height:243px">
    <div style="display:flex;height:42px;color:#fff;font-size:10.5px;font-weight:600">
      <div style="flex:1;background:var(--teal);display:flex;align-items:center;justify-content:center;box-shadow:0 4px 10px rgba(0,0,0,.3)">MODE 1</div>
      <div style="flex:1;background:var(--teal);display:flex;align-items:center;justify-content:center;border-left:1px solid #fff">MODE 2</div>
    </div>
    <div class="mini" style="padding:16px 30px 0">
      <div>Mode 1 &nbsp;&nbsp;&nbsp;&nbsp;: &nbsp;&nbsp; Mode 1 Name</div>
      <div style="text-align:center;color:var(--teal);margin-top:4px">SELECT</div>
      <div style="text-align:center;margin-top:10px"><span style="background:var(--teal);color:#fff;padding:8px 26px;display:inline-block;font-weight:600">PARAMETERS</span></div>
      <div style="margin-top:16px">Entry &nbsp;&nbsp;&nbsp;&nbsp;&nbsp;&nbsp;&nbsp;&nbsp;: &nbsp;&nbsp;0.5</div>
      <div style="margin-top:6px">Exit &nbsp;&nbsp;&nbsp;&nbsp;&nbsp;&nbsp;&nbsp;&nbsp;&nbsp;&nbsp;: &nbsp;&nbsp;-0.3</div>
      <div style="margin-top:6px">Lookback &nbsp;&nbsp;: &nbsp;&nbsp;5</div>
      <div style="text-align:center;color:var(--teal);margin-top:8px">RUN</div>
    </div>
  </div>

  <table class="grid" style="left:119px;top:476px;width:240px;background:#fff">
    <tr><th colspan="2" style="height:46px">STATS</th></tr>
    <tr><td style="height:45px">STAT 1</td><td>0.5</td></tr>
    <tr><td style="height:45px">STAT 2</td><td>-3</td></tr>
    <tr><td style="height:45px">STAT 3</td><td>30%</td></tr>
  </table>

  <div class="card" style="left:403px;top:180px;width:335px;height:246px;border:none">
    <svg width="335" height="246" viewBox="0 0 335 246">
      <text x="-150" y="-4" transform="rotate(-90)" font-size="10" fill="var(--teal)">PNL</text>
      <polyline fill="none" stroke="var(--teal)" stroke-width="1.6" points="4,216 20,200 40,196 60,198 80,186 100,170"/>
      <polyline fill="none" stroke="#e23b2b" stroke-width="1.6" points="100,170 120,150 135,156 150,142 165,146 180,136"/>
      <polyline fill="none" stroke="var(--teal)" stroke-width="1.6" points="180,136 200,140 215,112 235,118 250,100 270,108 290,80 305,92 320,72 335,82"/>
    </svg>
  </div>
  <div style="position:absolute;left:403px;top:430px;width:350px;display:flex;justify-content:space-between;font-size:10.5px;color:var(--teal)"><span>2014</span><span>2015</span><span>2016</span><span>2017</span><span>2018</span><span>2019</span></div>
  <div class="caption" style="left:403px;top:476px">Trades</div>
  <table class="grid" style="left:403px;top:511px;width:353px">
    <tr><th>OPEN</th><th>CLOSE</th><th>SIZE</th><th>RETURN</th></tr>
    <tr><td style="background:var(--row-alt)">3-4-2018</td><td style="background:var(--row-alt)">01-03-2018</td><td style="background:var(--row-alt)">13</td><td style="background:var(--row-alt)">5%</td></tr>
  </table>
  <p class="footer" style="top:722px">© Copyrights 2019 Pellworth | All Rights Reserved</p>
</section>

</body>
</html>
```